Firm Stationery Design

I need a design for stationery, including: Stationery First Page, Stationery Second Sheet, Envelope, Mailing Label for Flat Envelopes, and Business Cards

```html
<!DOCTYPE html>
<html lang="en">
<head>
<meta charset="utf-8">
<title>Harlow Law LLC — Stationery</title>
<link href="https://fonts.googleapis.com/css2?family=Montserrat:wght@400;500;700&display=swap" rel="stylesheet">
<style>
:root{
  --bg:#a4a4a4;
  --bg-light:#b5b3b4;
  --paper:#ffffff;
  --paper-soft:#f4f4f4;
  --ink:#1b1b1b;
  --text:#2b2b2b;
  --orange:#f5a01e;
  --orange-deep:#e38f15;
  --rule:#555;
  --shadow:0 3px 6px rgba(0,0,0,.28);
}
*{box-sizing:border-box;margin:0;padding:0}
html,body{width:1200px;height:957px;overflow:hidden}
body{background:var(--bg);font-family:"Montserrat",Arial,sans-serif;color:var(--text);position:relative}
.panel-light{position:absolute;left:651px;top:0;width:549px;height:523px;background:var(--bg-light)}
.sheet{position:absolute;background:var(--paper);box-shadow:var(--shadow)}
.card{border-radius:6px}

/* brand lockup */
.brand{display:flex;flex-direction:column;align-items:center;font-weight:700;color:var(--ink);line-height:1;font-size:var(--s)}
.brand__dot{width:calc(var(--s)*1.7);height:calc(var(--s)*1.7);background:var(--orange);margin-bottom:calc(var(--s)*.45)}
.brand__name{letter-spacing:.02em}
.brand__sub{font-size:.5em;letter-spacing:.6em;margin-top:.45em;padding-left:.6em}

.abs{position:absolute}
.divider{position:absolute;width:1px;background:var(--orange)}
.addr{line-height:1.45;color:var(--text)}
.contact{list-style:none;line-height:1.5}
.contact li{display:flex;align-items:center;gap:.35em}
.contact svg{width:.85em;height:.85em;fill:var(--orange);flex:none}
.accent{color:var(--orange)}

/* letter */
.letter__to{font-size:2.6px;line-height:1.5}
.letter__to b{font-weight:700}
.letter__body p{font-size:2.4px;line-height:1.6;margin-bottom:4px;text-align:justify}

/* notebook */
.rings{position:absolute;display:flex;flex-direction:column;justify-content:space-between}
.rings i{display:block;width:14px;height:3px;background:var(--ink);border-radius:2px}
.page{position:absolute;background:var(--paper-soft);box-shadow:var(--shadow)}
.page__date{position:absolute;right:6px;top:14px;font-size:4.5px;color:#444}
.page__lines{position:absolute;left:7px;right:7px;top:34px;bottom:10px;
  background:repeating-linear-gradient(to bottom,transparent 0,transparent 7.3px,var(--rule) 7.3px,var(--rule) 8px)}

.compliments{position:absolute;right:12px;bottom:10px;font-size:10.5px;color:var(--ink)}
</style>
</head>
<body>
<svg width="0" height="0" style="position:absolute" aria-hidden="true">
  <symbol id="i-phone" viewBox="0 0 24 24"><path d="M6.6 10.8a15 15 0 0 0 6.6 6.6l2.2-2.2c.3-.3.7-.4 1-.2 1.1.4 2.3.6 3.6.6.6 0 1 .4 1 1V20c0 .6-.4 1-1 1A17 17 0 0 1 3 4c0-.6.4-1 1-1h3.5c.6 0 1 .4 1 1 0 1.3.2 2.5.6 3.6.1.3 0 .7-.2 1z"/></symbol>
  <symbol id="i-mail" viewBox="0 0 24 24"><path d="M2 5h20v14H2z M2 5l10 7 10-7" /></symbol>
  <symbol id="i-web" viewBox="0 0 24 24"><circle cx="12" cy="12" r="10"/></symbol>
</svg>

<div class="panel-light"></div>

<!-- business card front -->
<div class="sheet card" style="left:78px;top:77px;width:165px;height:95px">
  <div class="brand abs" style="--s:15px;left:0;right:0;top:16px">
    <span class="brand__dot"></span><span class="brand__name">HARLOW</span><span class="brand__sub">LAW LLC</span>
  </div>
</div>

<!-- business card back -->
<div class="sheet card" style="left:78px;top:185px;width:165px;height:94px">
  <div class="brand abs" style="--s:10.5px;left:12px;top:21px">
    <span class="brand__dot"></span><span class="brand__name">HARLOW</span><span class="brand__sub">LAW LLC</span>
  </div>
  <div class="divider" style="left:79px;top:20px;height:54px"></div>
  <div class="abs" style="left:85px;top:20px;font-size:5px">
    <div style="font-size:7.2px;font-weight:700;color:var(--orange)">DANIEL REYES</div>
    <div style="margin-bottom:4px">Managing Director</div>
    <div class="addr" style="margin-bottom:3px">Your address, City<br>State, Zip 1234</div>
    <ul class="contact">
      <li><svg><use href="#i-phone"/></svg>123 456 789</li>
      <li><svg><use href="#i-mail"/></svg>info@harlowlawllc.com</li>
      <li><svg><use href="#i-web"/></svg>www.harlowlawllc.com</li>
    </ul>
  </div>
</div>

<!-- letterhead first page -->
<div class="sheet" style="left:257px;top:78px;width:141px;height:200px">
  <div class="brand abs" style="--s:6px;left:13px;top:9px">
    <span class="brand__dot"></span><span class="brand__name">HARLOW</span><span class="brand__sub">LAW LLC</span>
  </div>
  <div class="divider" style="left:91px;top:10px;height:20px"></div>
  <div class="abs" style="left:95px;top:10px;font-size:2.6px">
    <div class="addr">Your address, City<br>State, Zip 1234</div>
    <ul class="contact"><li><svg><use href="#i-phone"/></svg>123 456 789</li><li><svg><use href="#i-mail"/></svg>info@harlowlawllc.com</li><li><svg><use href="#i-web"/></svg>www.harlowlawllc.com</li></ul>
  </div>
  <div class="letter__to abs" style="left:13px;top:53px"><b>NORA ELLIS</b><br>Chief Executive Officer<br>City State, Zip Code</div>
  <div class="letter__body abs" style="left:13px;right:13px;top:76px">
    <p>Thank you for meeting with our team last week. We have reviewed the documents you shared and prepared a short summary of the next steps for your matter.</p>
    <p>Our office will contact the other party this month and keep you informed of every reply we receive.</p>
    <p>Please call us with any questions. We look forward to working with you.</p>
  </div>
  <div class="abs" style="left:13px;top:154px;font-size:2.4px">Sincerely,</div>
</div>

<!-- envelope front -->
<div class="sheet" style="left:412px;top:79px;width:209px;height:90px">
  <div class="brand abs" style="--s:6px;left:9px;top:9px">
    <span class="brand__dot"></span><span class="brand__name">HARLOW</span><span class="brand__sub">LAW LLC</span>
  </div>
  <div class="divider" style="left:36px;top:9px;height:20px"></div>
  <div class="addr abs" style="left:41px;top:10px;font-size:3.4px">Your address, City<br>State, Zip 1234</div>
</div>

<!-- envelope back -->
<div class="sheet" style="left:409px;top:184px;width:210px;height:93px">
  <svg class="abs" style="left:0;top:0" width="210" height="40" viewBox="0 0 210 40" aria-hidden="true">
    <path d="M2 1 Q6 33 22 34 L188 34 Q204 33 208 1" fill="none" stroke="#ddd" stroke-width="1"/>
  </svg>
  <div class="brand abs" style="--s:6px;left:0;right:0;top:7px">
    <span class="brand__dot"></span><span class="brand__name">HARLOW</span>
  </div>
</div>

<!-- notebook cover -->
<div class="sheet" style="left:78px;top:309px;width:140px;height:200px">
  <div class="rings" style="left:-6px;top:6px;bottom:6px"><i></i><i></i><i></i><i></i><i></i><i></i><i></i><i></i><i></i><i></i><i></i><i></i><i></i><i></i><i></i><i></i><i></i></div>
  <div class="brand abs" style="--s:19px;left:8px;right:0;top:48px">
    <span class="brand__dot"></span><span class="brand__name">HARLOW</span><span class="brand__sub">LAW LLC</span>
  </div>
</div>

<!-- notebook spread -->
<div class="page" style="left:302px;top:311px;width:140px;height:197px">
  <div class="brand abs" style="--s:5px;left:7px;top:6px"><span class="brand__dot"></span><span class="brand__name">HARLOW</span><span class="brand__sub">LAW LLC</span></div>
  <div class="page__date">Date......./......./.......</div>
  <div class="page__lines"></div>
</div>
<div class="page" style="left:442px;top:311px;width:140px;height:197px">
  <div class="brand abs" style="--s:5px;left:8px;top:6px"><span class="brand__dot"></span><span class="brand__name">HARLOW</span><span class="brand__sub">LAW LLC</span></div>
  <div class="page__date">Date......./......./.......</div>
  <div class="page__lines"></div>
</div>
<div class="rings" style="left:435px;top:316px;bottom:455px"><i></i><i></i><i></i><i></i><i></i><i></i><i></i><i></i><i></i><i></i><i></i><i></i><i></i><i></i><i></i><i></i><i></i><i></i><i></i><i></i></div>

<!-- presentation folder, outside -->
<div class="sheet" style="left:775px;top:50px;width:300px;height:200px">
  <div class="brand abs" style="--s:17px;left:18px;top:30px">
    <span class="brand__dot"></span><span class="brand__name">HARLOW</span><span class="brand__sub">LAW LLC</span>
  </div>
  <div class="addr abs" style="left:82px;top:158px;font-size:4.6px;text-align:right">Your address, City<br>State, Zip 1234</div>
  <ul class="contact abs" style="left:12px;top:168px;font-size:4.6px">
    <li><svg><use href="#i-phone"/></svg>123 456 789</li><li><svg><use href="#i-mail"/></svg>info@harlowlawllc.com</li><li><svg><use href="#i-web"/></svg>www.harlowlawllc.com</li>
  </ul>
  <div class="abs" style="left:150px;top:0;width:1px;height:200px;background:#e4e4e4"></div>
  <div class="abs" style="left:186px;top:52px;width:78px;height:78px;background:var(--orange)"></div>
</div>

<!-- presentation folder, inside -->
<div class="sheet" style="left:775px;top:285px;width:300px;height:200px;background:#f0f0f0;overflow:hidden">
  <div class="abs" style="left:150px;top:0;width:1px;height:200px;background:#d6d6d6"></div>
  <div class="sheet" style="left:170px;top:10px;width:112px;height:160px;box-shadow:0 1px 3px rgba(0,0,0,.2)">
    <div class="brand abs" style="--s:5px;left:9px;top:8px"><span class="brand__dot"></span><span class="brand__name">HARLOW</span><span class="brand__sub">LAW LLC</span></div>
    <div class="divider" style="left:72px;top:8px;height:16px"></div>
    <div class="abs" style="left:75px;top:8px;font-size:2.2px"><div class="addr">Your address, City<br>State, Zip 1234</div><ul class="contact"><li><svg><use href="#i-phone"/></svg>123 456 789</li><li><svg><use href="#i-mail"/></svg>info@harlowlawllc.com</li><li><svg><use href="#i-web"/></svg>www.harlowlawllc.com</li></ul></div>
    <div class="letter__body abs" style="left:9px;right:9px;top:44px"><p>Thank you for choosing our firm. We will review your file and reply soon.</p></div>
  </div>
  <svg class="abs" style="left:0;top:0" width="300" height="200" viewBox="0 0 300 200" aria-hidden="true">
    <path d="M0 140 L130 118 Q140 116 142 126 L150 200 L0 200Z" fill="var(--ink)"/>
    <path d="M150 200 L158 128 Q160 120 170 120 L300 120 L300 200Z" fill="var(--orange)"/>
  </svg>
</div>

<!-- large flat envelope -->
<div class="sheet" style="left:78px;top:586px;width:357px;height:268px">
  <div class="brand abs" style="--s:12px;left:25px;top:24px">
    <span class="brand__dot"></span><span class="brand__name">HARLOW</span><span class="brand__sub">LAW LLC</span>
  </div>
  <div class="divider" style="left:90px;top:24px;height:50px"></div>
  <div class="addr abs" style="left:99px;top:28px;font-size:9px">Your address, City<br>State, Zip 1234</div>
</div>

<!-- second sheet -->
<div class="sheet" style="left:480px;top:586px;width:198px;height:264px">
  <div class="brand abs" style="--s:9.5px;left:16px;top:17px">
    <span class="brand__dot"></span><span class="brand__name">HARLOW</span><span class="brand__sub">LAW LLC</span>
  </div>
  <div class="divider" style="left:65px;top:17px;height:40px"></div>
  <div class="addr abs" style="left:71px;top:20px;font-size:6.5px">Your address, City<br>State, Zip 1234</div>
</div>

<!-- mailing label -->
<div class="sheet" style="left:811px;top:571px;width:275px;height:130px">
  <div class="brand abs" style="--s:20px;left:0;right:0;top:20px">
    <span class="brand__dot"></span><span class="brand__name">HARLOW</span><span class="brand__sub">LAW LLC</span>
  </div>
</div>

<!-- compliments slip -->
<div class="sheet" style="left:808px;top:734px;width:275px;height:130px">
  <div class="brand abs" style="--s:15px;left:9px;top:14px">
    <span class="brand__dot"></span><span class="brand__name">HARLOW</span><span class="brand__sub">LAW LLC</span>
  </div>
  <div class="abs" style="left:204px;top:31px;font-size:5.3px">
    <div class="addr" style="margin-bottom:4px">Your address, City<br>State, Zip 1234</div>
    <ul class="contact"><li><svg><use href="#i-phone"/></svg>123 456 789</li><li><svg><use href="#i-mail"/></svg>info@harlowlawllc.com</li><li><svg><use href="#i-web"/></svg>www.harlowlawllc.com</li></ul>
  </div>
  <div class="compliments">with <span class="accent">compliments</span></div>
</div>
</body>
</html>
```